New Web Design Project

Number of Pages Required

1 page

Requirements
Must have
• An Overview / Background of the Business & Services(not for profit rescue animal farm)
• The Target Market / Audience you are trying to reach (animal lovers)
• Design Specifics; any preferences or ideas for Style, Colour, Imagery, etc (no preferences)

```html
<!DOCTYPE html>
<html lang="en">
<head>
<meta charset="utf-8">
<title>Cedar Hollow Farms</title>
<link href="https://fonts.googleapis.com/css2?family=Lato:wght@400;700;900&display=swap" rel="stylesheet">
<style>
:root{
  --brown:#6b3f14;
  --brown-dark:#5a3311;
  --green:#2f8a14;
  --green-bright:#3a9a1a;
  --text:#555;
  --light:#f2f2f2;
  --footer:#2a2a2a;
  --white:#fff;
}
*{margin:0;padding:0;box-sizing:border-box}
html,body{width:1200px;height:3158px;overflow:hidden}
body{font-family:'Lato',sans-serif;color:var(--text);background:var(--white);position:relative}
section,header,footer{position:absolute;left:0;width:1200px}
.btn{position:absolute;display:flex;align-items:center;justify-content:center;background:var(--green);color:var(--white);font-weight:700;font-size:15px;letter-spacing:.5px;text-transform:uppercase;text-decoration:none}

/* header */
.site-header{top:0;height:95px;background:var(--white)}
.brand{position:absolute;left:74px;top:26px;font-size:36px;font-weight:700;color:var(--brown)}
.main-nav{position:absolute;right:74px;top:38px;display:flex;gap:40px}
.main-nav a{font-size:13.5px;text-transform:uppercase;color:#333;text-decoration:none}
.main-nav a.active{color:var(--green)}

/* hero */
.hero{top:95px;height:553px;text-align:center;color:var(--white)}
.hero-photo{position:absolute;inset:0;background:linear-gradient(180deg,#3f6b1e 0%,#5f9a2c 35%,#4d7d22 60%,#3a2a18 100%)}
.hero-title{position:absolute;top:236px;width:100%;font-size:50px;font-weight:900;text-transform:uppercase}
.hero-sub{position:absolute;top:300px;width:100%;font-size:21px}
.hero .btn{left:512px;top:351px;width:176px;height:51px}
.dots{position:absolute;top:501px;left:0;width:100%;display:flex;justify-content:center;gap:12px}
.dots span{width:11px;height:11px;border-radius:50%;background:var(--white)}

/* overview */
.overview{top:648px;height:342px;text-align:center}
.section-title{font-size:30px;font-weight:700;text-transform:uppercase;color:var(--brown)}
.overview .section-title{position:absolute;top:46px;width:100%}
.overview p{position:absolute;top:100px;left:90px;width:1020px;font-size:15px;line-height:31px}
.overview .btn{left:510px;top:234px;width:180px;height:47px}

/* services */
.services{top:990px;height:694px;background:var(--light)}
.services-intro{position:absolute;left:0;top:67px;width:421px;height:564px;background:var(--brown);color:var(--white);text-align:center}
.services-intro h2{margin-top:160px;font-size:29px;font-weight:700;text-transform:uppercase;line-height:34px}
.services-intro p{margin:26px auto 0;width:340px;font-size:15px;line-height:27px}
.services-intro .btn{left:140px;top:343px;width:180px;height:47px}
.service-card{position:absolute;width:332px;height:272px;color:var(--white);text-align:center;overflow:hidden}
.service-card .photo{position:absolute;inset:0}
.service-card .shade{position:absolute;inset:0;background:rgba(30,30,30,.45)}
.service-card h3{position:relative;margin-top:62px;font-size:23px;font-weight:700;text-transform:uppercase}
.service-card p{position:relative;margin:10px auto 0;width:290px;font-size:14.5px;line-height:26px}
.c1{left:438px;top:67px}.c2{left:792px;top:67px}.c3{left:438px;top:359px}.c4{left:792px;top:359px}

/* blog */
.blog{top:1684px;height:354px;text-align:center}
.blog .section-title{position:absolute;top:56px;width:100%}
.post{position:absolute;top:114px;width:300px}
.post h3{font-size:20px;font-weight:700;color:var(--brown);line-height:27px}
.post p{margin-top:10px;font-size:15px;line-height:27px}
.post a{display:block;margin-top:12px;font-size:15px;font-weight:700;color:var(--green);text-decoration:none}
.p1{left:90px}.p2{left:450px}.p3{left:810px}

/* gallery */
.gallery{top:2038px;height:646px}
.gallery-band{position:absolute;left:0;top:0;width:1200px;height:294px;background:linear-gradient(90deg,#2f8a14 0%,#3f7a14 50%,#6b3f14 100%)}
.gallery .section-title{position:absolute;top:44px;width:100%;text-align:center;color:var(--white)}
.tile{position:absolute;width:339px;height:221px}
.g1{left:76px;top:118px;background:linear-gradient(135deg,#7a5a44,#c9c2b8)}
.g2{left:432px;top:118px;background:linear-gradient(180deg,#8fb26a,#b4a999)}
.g3{left:786px;top:118px;background:linear-gradient(180deg,#e8b8a8,#c99a3c)}
.g4{left:76px;top:360px;background:linear-gradient(135deg,#8a7054,#3a4a8a)}
.g5{left:432px;top:360px;background:linear-gradient(180deg,#3b7fd0,#8a6a4a)}
.g6{left:786px;top:360px;background:linear-gradient(135deg,#6aa03a,#4a2e1a)}

/* mailing */
.mailing{top:2684px;height:280px;text-align:center;color:var(--white)}
.mailing-photo{position:absolute;inset:0;background:linear-gradient(180deg,#2c2a1c 0%,#3d4a22 50%,#2a2216 100%)}
.mailing h2{position:absolute;top:56px;width:100%;font-size:25px;font-weight:700;text-transform:uppercase}
.field{position:absolute;top:112px;width:330px;height:38px;background:var(--white);color:#444;font-size:13px;padding:11px 14px;text-align:left}
.f1{left:255px}.f2{left:615px}
.mailing .btn{left:510px;top:175px;width:180px;height:48px}

/* footer */
.site-footer{top:2964px;height:194px;background:var(--footer);color:var(--white);text-align:center}
.footer-nav{position:absolute;top:48px;width:100%;display:flex;justify-content:center;gap:46px}
.footer-nav a{font-size:13.5px;text-transform:uppercase;color:var(--white);text-decoration:none}
.copyright{position:absolute;top:87px;width:100%;font-size:13px;color:#aaa}
.social{position:absolute;top:120px;width:100%;display:flex;justify-content:center;gap:18px}
.social span{width:18px;height:18px;border-radius:50%;background:var(--white)}
</style>
</head>
<body>

<header class="site-header">
  <div class="brand">Cedar Hollow Farms</div>
  <nav class="main-nav">
    <a class="active" href="#">Home</a>
    <a href="#">Company Overview</a>
    <a href="#">Services</a>
    <a href="#">Blog</a>
    <a href="#">Careers</a>
    <a href="#">Contact Us</a>
  </nav>
</header>

<section class="hero">
  <div class="hero-photo" role="img" aria-label="Sheep grazing on a sunny green pasture behind a wooden fence"></div>
  <h1 class="hero-title">Cedar Hollow Farms</h1>
  <p class="hero-sub">Vestibulum pretium libero urna, luctus dignissim ante convallis eu...</p>
  <a class="btn" href="#">Read More</a>
  <div class="dots"><span></span><span></span><span></span></div>
</section>

<section class="overview">
  <h2 class="section-title">Company Overview</h2>
  <p>Lorem ipsum dolor sit amet, consectetur adipiscing elit. Fusce non sapien gravida, imperdiet nunc vehicula, gravida tellus. Proin gravida interdum risus, vel aliquet neque cursus sed. Duis non maximus risus. Mauris ipsum massa, feugiat sed metus non, dictum dignissim erat. Nulla aliquam eget lectus quis sollicitudin. Donec posuere finibus nisl, in congue orci ultricies nec.</p>
  <a class="btn" href="#">Read More</a>
</section>

<section class="services">
  <div class="services-intro">
    <h2>Serving Project<br>Events</h2>
    <p>Etiam tellus quam, rhoncus in feugiat a, accumsan in arcu. Donec luctus lorem nunc, in blandit dolor imperdiet id.</p>
    <a class="btn" href="#">View All Services</a>
  </div>
  <div class="service-card c1">
    <div class="photo" role="img" aria-label="Volunteer caring for a horse" style="background:linear-gradient(135deg,#5a5046,#2e2a26)"></div>
    <div class="shade"></div>
    <h3>Nulla Aliquam Eget</h3>
    <p>Donec posuere finibus nisl, in congue orci ultricies nec pellentesque ipsumduis mauris massa, ultrices quis velit ac, sollicitudin placerat nisl..</p>
  </div>
  <div class="service-card c2">
    <div class="photo" role="img" aria-label="Hand feeding a goat" style="background:linear-gradient(135deg,#6a6a60,#3a3830)"></div>
    <div class="shade"></div>
    <h3>Nulla Aliquam Eget</h3>
    <p>Donec posuere finibus nisl, in congue orci ultricies nec pellentesque ipsumduis mauris massa, ultrices quis velit ac, sollicitudin placerat nisl..</p>
  </div>
  <div class="service-card c3">
    <div class="photo" role="img" aria-label="Farmer feeding chickens in a yard" style="background:linear-gradient(135deg,#6a5a3a,#4a3a22)"></div>
    <div class="shade"></div>
    <h3>Nulla Aliquam Eget</h3>
    <p>Donec posuere finibus nisl, in congue orci ultricies nec pellentesque ipsumduis mauris massa, ultrices quis velit ac, sollicitudin placerat nisl..</p>
  </div>
  <div class="service-card c4">
    <div class="photo" role="img" aria-label="Hand scattering feed for a hen" style="background:linear-gradient(135deg,#5a6a3a,#22304a)"></div>
    <div class="shade"></div>
    <h3>Nulla Aliquam Eget</h3>
    <p>Donec posuere finibus nisl, in congue orci ultricies nec pellentesque ipsumduis mauris massa, ultrices quis velit ac, sollicitudin placerat nisl..</p>
  </div>
</section>

<section class="blog">
  <h2 class="section-title">Blog Posts</h2>
  <article class="post p1">
    <h3>Nulla aliquam eget lectus quis sollicitudin.</h3>
    <p>Lorem ipsum dolor sit amet, consectetur adipiscing elit. Fusce non sapien gravida, imperdiet nunc vehicula..</p>
    <a href="#">View Full Posts &gt;&gt;</a>
  </article>
  <article class="post p2">
    <h3>Nulla aliquam eget lectus quis sollicitudin.</h3>
    <p>Lorem ipsum dolor sit amet, consectetur adipiscing elit. Fusce non sapien gravida, imperdiet nunc vehicula..</p>
    <a href="#">View Full Posts &gt;&gt;</a>
  </article>
  <article class="post p3">
    <h3>Nulla aliquam eget lectus quis sollicitudin.</h3>
    <p>Lorem ipsum dolor sit amet, consectetur adipiscing elit. Fusce non sapien gravida, imperdiet nunc vehicula..</p>
    <a href="#">View Full Posts &gt;&gt;</a>
  </article>
</section>

<section class="gallery">
  <div class="gallery-band"></div>
  <h2 class="section-title">Gallery</h2>
  <div class="tile g1" role="img" aria-label="Rescued cat held beside a cage"></div>
  <div class="tile g2" role="img" aria-label="Flock of sheep in a field"></div>
  <div class="tile g3" role="img" aria-label="Piglets on straw"></div>
  <div class="tile g4" role="img" aria-label="Volunteer hugging a dog"></div>
  <div class="tile g5" role="img" aria-label="Cows under a blue sky"></div>
  <div class="tile g6" role="img" aria-label="Two horses on grass"></div>
</section>

<section class="mailing">
  <div class="mailing-photo" role="img" aria-label="Wooden fence along a shaded pasture"></div>
  <h2>Join Our Mailing List</h2>
  <div class="field f1">Enter Name</div>
  <div class="field f2">Enter Email Address</div>
  <a class="btn" href="#">Subscribe Now</a>
</section>

<footer class="site-footer">
  <nav class="footer-nav">
    <a href="#">Home</a>
    <a href="#">Company Overview</a>
    <a href="#">Services</a>
    <a href="#">Blog</a>
    <a href="#">Careers</a>
    <a href="#">Contact Us</a>
  </nav>
  <p class="copyright">Copyright © 2019. Company Name. All Right Reserved</p>
  <div class="social" aria-label="Social links">
    <span></span><span></span><span></span><span></span><span></span><span></span>
  </div>
</footer>

</body>
</html>
```